Verlindo Magician

I want the business card for my business to give to people who watch that later I will be employed to show magic here is my website http://www.balsamomagicien.com/I want the interesting design , i am very opened for formal and informal, I watch a lot of design so don't stick to the common shape and form but i hope it can also be produced the thing to write on will be the same as in picture that i will upload , i also will upload the logo for you that so can be easy to useDenis CostilleMagicianMAGICIAN VERLINDO 17 rue des Tilleuls - 25000 BESANÇON contact@verlindoillusions.example tel. 0381 946 157 tel. 0674 219 503

```html
<!DOCTYPE html>
<html lang="en">
<head>
<meta charset="utf-8">
<title>Verlindo Magician – Business Card</title>
<link href="https://fonts.googleapis.com/css2?family=Jost:wght@400&display=swap" rel="stylesheet">
<style>
  :root {
    --stage: #e4e3e1;
    --paper: #ffffff;
    --ink: #111111;
    --red: #e52421;
    --grey: #555555;
    --rule: #8a8a8a;
  }
  * { margin: 0; padding: 0; box-sizing: border-box; }
  html, body {
    width: 1125px; height: 1200px; overflow: hidden;
    background: var(--stage);
    font-family: "Jost", sans-serif;
  }
  .card {
    position: absolute; left: 150px;
    width: 800px; height: 456px;
    transform: scale(1.032); transform-origin: top left;
    box-shadow: 0 3px 8px rgba(0,0,0,.25);
    overflow: hidden;
  }
  .card--front { top: 106px; background: var(--paper); }
  .card--back  { top: 640px; background: var(--red); }

  .swoosh { position: absolute; left: 0; top: 0; width: 800px; height: 456px; }

  .brand-name {
    position: absolute; left: 590px; top: 205px; width: 175px;
    text-align: center; font-size: 31px; letter-spacing: 1px; color: var(--ink);
  }

  .holder { position: absolute; left: 38px; top: 244px; }
  .holder__name { font-size: 30px; color: var(--ink); line-height: 1.1; }
  .holder__role { font-size: 20px; color: var(--red); line-height: 1.2; }

  .divider {
    position: absolute; left: 38px; top: 325px; width: 714px;
    border-top: 1px solid var(--rule);
  }

  .contacts {
    position: absolute; left: 38px; top: 342px;
    list-style: none; font-size: 19px; color: var(--grey); line-height: 26px;
  }
  .contacts li { display: flex; align-items: center; gap: 10px; }
  .contacts svg { width: 16px; height: 16px; fill: var(--ink); flex: none; }

  .studio {
    position: absolute; right: 44px; top: 342px;
    text-align: right; font-size: 19px; color: var(--grey); line-height: 26px;
  }
  .studio__name { color: var(--red); }
  .studio__web { letter-spacing: 2.4px; }

  .back-name {
    position: absolute; left: 0; top: 170px; width: 800px;
    text-align: center; font-size: 52px; letter-spacing: 3px; color: var(--ink);
  }
  .back-web {
    position: absolute; left: 0; top: 396px; width: 800px;
    text-align: center; font-size: 18px; letter-spacing: 3px; color: #ffffff;
  }
</style>
</head>
<body>

<section class="card card--front">
  <svg class="swoosh" viewBox="0 0 800 456" aria-hidden="true">
    <path d="M0,0 H550 C350,18 70,78 0,172 Z" fill="var(--ink)"/>
    <path d="M0,232 C40,140 300,38 550,0 C360,26 75,96 0,182 Z" fill="var(--red)"/>
  </svg>

  <div class="brand-name">VERLINDO</div>

  <div class="holder">
    <div class="holder__name">Marc Ravoulet</div>
    <div class="holder__role">Magician</div>
  </div>

  <div class="divider"></div>

  <ul class="contacts">
    <li>
      <svg viewBox="0 0 24 24"><path d="M6.6 10.8a15.1 15.1 0 0 0 6.6 6.6l2.2-2.2c.3-.3.7-.4 1-.2 1.1.4 2.3.6 3.6.6.6 0 1 .4 1 1V20c0 .6-.4 1-1 1C10.6 21 3 13.4 3 4c0-.6.4-1 1-1h3.5c.6 0 1 .4 1 1 0 1.3.2 2.5.6 3.6.1.3 0 .7-.2 1z"/></svg>
      0381 946 157
    </li>
    <li>
      <svg viewBox="0 0 24 24"><path d="M6.6 10.8a15.1 15.1 0 0 0 6.6 6.6l2.2-2.2c.3-.3.7-.4 1-.2 1.1.4 2.3.6 3.6.6.6 0 1 .4 1 1V20c0 .6-.4 1-1 1C10.6 21 3 13.4 3 4c0-.6.4-1 1-1h3.5c.6 0 1 .4 1 1 0 1.3.2 2.5.6 3.6.1.3 0 .7-.2 1z"/></svg>
      0674 219 503
    </li>
    <li>
      <svg viewBox="0 0 24 24"><path d="M2 5h20v14H2z M3.5 6.5 12 13l8.5-6.5" fill="var(--ink)"/><path d="M3 6l9 7 9-7" fill="none" stroke="#fff" stroke-width="1.5"/></svg>
      contact@verlindoillusions.example
    </li>
  </ul>

  <div class="studio">
    <div class="studio__name">MAGICIAN VERLINDO</div>
    <div class="studio__address">17 rue des Tilleuls - 25000 BESANÇON</div>
    <div class="studio__web">www.verlindoillusions.example</div>
  </div>
</section>

<section class="card card--back">
  <div class="back-name">VERLINDO</div>
  <div class="back-web">www.verlindoillusions.example</div>
</section>

</body>
</html>
```